Business Card for beauty technology startup

Design Glimora Business Card for a Beauty, based on the website identity and colors (https://www.glimora-example.com).
Glimora is a beauty tech startup that gathers helpful product info for beauty lovers and consumers (such as availability on stores, price range and product reviews) for makeup products. The card design must be young, colorful but clean, and very modern.

Target Market(s)

woman, 15-35

Industry/Entity Type

Cosmetics

Contact Information for Business Card

Full Name, address, phone

Font styles to use
Other font styles liked:
• Advent Pro

Colors
e34297
86cfc6
ffffff
5c5c5c
e8e8e8
e667a6
b2b2b2

Requirements
Must have
• One full colored side with a creative design and another with card info
• Use Color palette: #95C5C5 and/or #D38AA5
• Use fonts: Advent Pro
• Use website identity: https://www.glimora-example.com
Nice to have
• If needed extra font: Roboto

```html
<!DOCTYPE html>
<html lang="en">
<head>
<meta charset="utf-8">
<title>Glimora Business Card</title>
<link rel="stylesheet" href="https://fonts.googleapis.com/css2?family=Advent+Pro:wght@300;400;500&display=swap">
<style>
  :root {
    --backdrop: #e6e6e6;
    --rose: #c97e99;
    --rose-deep: #bf7090;
    --rose-text: #c27891;
    --ink: #2e2a2c;
    --teal: #7cb8ba;
    --paper: #f7f7f5;
  }
  * { margin: 0; padding: 0; box-sizing: border-box; }
  html, body {
    width: 1200px; height: 576px; overflow: hidden;
    background: var(--backdrop);
    font-family: "Advent Pro", sans-serif;
  }
  .canvas { position: relative; width: 1200px; height: 576px; }
  .card {
    position: absolute; top: 138px; width: 484px; height: 294px;
    border-radius: 12px; overflow: hidden;
  }
  .card--front {
    left: 82px;
    background: linear-gradient(180deg, var(--rose) 0%, var(--rose-deep) 100%);
  }
  .card--info { left: 602px; background: var(--paper); }

  .front-ring {
    position: absolute; left: 105px; top: 108px; width: 52px; height: 52px;
    border: 1.5px solid var(--ink); border-radius: 50%;
  }
  .front-name {
    position: absolute; left: 194px; top: 112px;
    font-size: 36px; font-weight: 300; letter-spacing: 5px;
    color: var(--ink); text-transform: uppercase; line-height: 1;
  }

  .info-name {
    position: absolute; left: 18px; top: 26px;
    font-size: 40px; font-weight: 300; letter-spacing: 6px;
    color: var(--rose-text); text-transform: uppercase; line-height: 1;
  }
  .info-ring {
    position: absolute; left: 228px; top: 20px; width: 256px; height: 256px;
    border: 4px solid var(--rose-text); border-radius: 50%;
  }
  .person {
    position: absolute; left: 19px; top: 150px;
    font-size: 21px; font-weight: 500; letter-spacing: 1px;
    color: var(--teal); text-transform: uppercase;
  }
  .address {
    position: absolute; left: 19px; top: 184px;
    font-size: 13px; line-height: 17px; color: var(--rose-text); font-weight: 500;
  }
  .contacts { position: absolute; left: 19px; top: 224px; list-style: none; }
  .contacts li {
    display: flex; align-items: center; gap: 8px;
    font-size: 13px; line-height: 16.5px; color: var(--rose-text); font-weight: 500;
  }
  .contacts svg { width: 11px; height: 11px; flex: none; }
</style>
</head>
<body>
<main class="canvas">
  <section class="card card--front" aria-label="Card front">
    <span class="front-ring" aria-hidden="true"></span>
    <h1 class="front-name">Glimora</h1>
  </section>

  <section class="card card--info" aria-label="Card back with contact details">
    <h2 class="info-name">Glimora</h2>
    <span class="info-ring" aria-hidden="true"></span>
    <p class="person">Mara Ellison</p>
    <p class="address">123, Street Number, City Name,<br>Country - 123456</p>
    <ul class="contacts">
      <li>
        <svg viewBox="0 0 12 12" aria-hidden="true"><path d="M2.5 1 L4.5 1 L5.3 3.5 L4 4.6 Q5 7 7.4 8 L8.5 6.7 L11 7.5 L11 9.5 Q10.5 11 9 11 Q1 10 1 2.5 Q1 1 2.5 1 Z" fill="none" stroke="var(--teal)" stroke-width="1.2"/></svg>
        00 444 555 666
      </li>
      <li>
        <svg viewBox="0 0 12 12" aria-hidden="true"><g fill="none" stroke="var(--teal)" stroke-width="1.3"><rect x="0.8" y="5.2" width="6" height="3.2" rx="1.6" transform="rotate(-45 3.8 6.8)"/><rect x="5.2" y="3.6" width="6" height="3.2" rx="1.6" transform="rotate(-45 8.2 5.2)"/></g></svg>
        www.glimora-example.com
      </li>
      <li>
        <svg viewBox="0 0 12 12" aria-hidden="true"><g fill="none" stroke="var(--teal)" stroke-width="1.2"><rect x="0.8" y="2.3" width="10.4" height="7.4"/><path d="M0.8 2.3 L6 6.6 L11.2 2.3"/></g></svg>
        yourname@glimora-example.com
      </li>
    </ul>
  </section>
</main>
</body>
</html>
```